Business Card Design

New business card design

Target Market(s)

Residential & Commercial Property Managers

Industry/Entity Type

Plumbing Services

Contact Information for Business Card

Name - Rowan Keddle, title - Director, Phone Number - 0431 286 517, email - rowan@tbk-plumbing.com.au, Company ABN - 73 215 904 386,

Font styles to use
Sans Serif

Colors
0054AA
0677BA
7BADD7
CADEEF
E8F1F8

```html
<!DOCTYPE html>
<html lang="en">
<head>
<meta charset="utf-8">
<title>TBK Plumbing Services – Business Card</title>
<link rel="stylesheet" href="https://fonts.googleapis.com/css2?family=Montserrat:wght@300;400;600&display=swap">
<style>
  :root {
    --backdrop: #1b1c1e;
    --card-light: #f4f4f3;
    --card-dark: #1d232a;
    --ink: #1e252c;
    --accent: #2aa3db;
    --muted: #55595d;
    --white: #ffffff;
  }
  * { margin: 0; padding: 0; box-sizing: border-box; }
  html, body {
    width: 1200px; height: 1059px; overflow: hidden;
    background: var(--backdrop);
    font-family: "Montserrat", sans-serif;
  }
  .canvas { position: relative; width: 1200px; height: 1059px; }

  .card {
    position: absolute;
    border-radius: 18px;
    overflow: hidden;
  }
  .card--front {
    left: 256px; top: 89px; width: 688px; height: 390px;
    background: var(--card-light);
    color: var(--ink);
  }
  .card--back {
    left: 254px; top: 547px; width: 693px; height: 393px;
    background: var(--card-dark);
  }

  /* brand wordmark */
  .brand { position: absolute; font-weight: 300; line-height: 1; }
  .brand__name { display: block; letter-spacing: 0.04em; }
  .brand__tagline { display: block; letter-spacing: 0.78em; white-space: nowrap; }

  .card--front .brand { left: 43px; top: 52px; color: var(--ink); }
  .card--front .brand__name { font-size: 70px; }
  .card--front .brand__tagline { font-size: 11px; margin-top: 24px; padding-left: 13px; }

  .card--back .brand {
    left: 0; right: 0; top: 112px; text-align: center; color: var(--white);
  }
  .card--back .brand__name { font-size: 100px; }
  .card--back .brand__tagline { font-size: 15px; margin-top: 36px; padding-left: 0.78em; }

  /* contact block */
  .marker {
    position: absolute; left: 0; top: 198px; width: 19px; height: 40px;
    background: var(--accent);
  }
  .person { position: absolute; left: 43px; top: 194px; }
  .person__name {
    font-size: 26px; font-weight: 600; color: var(--accent); line-height: 1.1;
  }
  .person__title { font-size: 16px; font-weight: 400; line-height: 1.2; }

  .abn {
    position: absolute; left: 43px; top: 259px;
    font-size: 16.5px; font-weight: 400; letter-spacing: 0.02em;
  }
  .abn__label { color: var(--accent); }

  .contacts { position: absolute; left: 43px; top: 303px; list-style: none; }
  .contacts__item {
    display: flex; align-items: center; gap: 8px;
    font-size: 16.5px; font-weight: 400; height: 26px; letter-spacing: 0.01em;
  }
  .contacts__icon { width: 12px; height: 12px; flex: none; }
</style>
</head>
<body>
<div class="canvas">

  <section class="card card--front" aria-label="Business card front">
    <div class="brand">
      <span class="brand__name">tbk</span>
      <span class="brand__tagline">plumbing services</span>
    </div>

    <div class="marker"></div>
    <div class="person">
      <p class="person__name">Rowan Keddle</p>
      <p class="person__title">Director</p>
    </div>

    <p class="abn"><span class="abn__label">Company ABN</span> - 73 215 904 386</p>

    <ul class="contacts">
      <li class="contacts__item">
        <svg class="contacts__icon" viewBox="0 0 24 24" aria-hidden="true">
          <path fill="#2aa3db" d="M6.6 10.8c1.4 2.8 3.8 5.1 6.6 6.6l2.2-2.2c.3-.3.7-.4 1-.2 1.1.4 2.3.6 3.6.6.6 0 1 .4 1 1V20c0 .6-.4 1-1 1C10.6 21 3 13.4 3 4c0-.6.4-1 1-1h3.5c.6 0 1 .4 1 1 0 1.3.2 2.5.6 3.6.1.3 0 .7-.2 1l-2.3 2.2z"/>
        </svg>
        <span>0431 286 517</span>
      </li>
      <li class="contacts__item">
        <svg class="contacts__icon" viewBox="0 0 24 24" aria-hidden="true">
          <rect x="1" y="4" width="22" height="16" fill="#2aa3db"/>
          <path d="M1 4l11 9 11-9M1 20l8-8M23 20l-8-8" stroke="#f4f4f3" stroke-width="1.6" fill="none"/>
        </svg>
        <span>rowan@tbk-plumbing.com.au</span>
      </li>
    </ul>
  </section>

  <section class="card card--back" aria-label="Business card back">
    <div class="brand">
      <span class="brand__name">tbk</span>
      <span class="brand__tagline">plumbing services</span>
    </div>
  </section>

</div>
</body>
</html>
```